Music Producer Website

I need a website designed for my music production company. We specialize in finding talented musicians and matching them with music producers all over the United States. A visitor can create a profile and/or upload their music demo and we submit it to thousands of music producers and production companies for review. In many cases, our members will receive multiple signing offers from music producers allowing them to choose the contract that is best for them. "We turn aspiring musicians into SuperStars!"
Please include photos that reflect all genres of music (black artists, white artists, both male and female.) We produce all types of music including rap, R&B, rock, country, and Hip Hop.
When a user creates a profile, they become visible to thousands of record producers who are looking to sign new talent and make them stars.
Somewhere in the top half of the page, please include a small form that the visitor can fill out. The form should look as follows:
Title (large and bold): Contact Us or Submit Music Demo
Fields to include (* = required): First Name*, Last Name*, Age, Zip Code, Email Address*, Daytime Phone, Evening Phone, Comments
Then, there will be a "submit" button to proceed to next step of form. Just below the "submit" button, should be the following verbiage: "After submitting, you will have the opportunity to upload demos of your music (optional) and provide other pertinent information about yourself, band, or group."
Updates
Reason: I have not seen a design that I am 100% satisfied with yet. Ideally, rotating header images (GIF or other) with several different music producers in studio (male, female, black, white) would be perfect. Here are some examples of how the header pics could look:
http://files.quillmarsh.net/art_img/514302/806421/806421_7391046_514302_image.jpg
http://files.quillmarsh.net/art_img/514302/806421/806421_7391058_514302_image.jpg
http://files.quillmarsh.net/art_img/514302/806421/806421_7391037_514302_image.jpg
Also, there should be a form on the site (somewhere in upper half of the page) with the following headline:
GET FOUND AND BECOME A STAR! (super large, super-bold font)
Contact Us or Submit Your Music for Review (large font, not as bold as headline)
First Name
Last Name
Age
Zip Code
Email Address
Daytime Phone
Evening Phone
Comments
Target Market(s)
We are targeting all types of musicians including rock, rap, pop, R&B, country, gospel, etc.
Industry/Entity Type
Artists
Colors
Designer to choose colors to be used in the design.
Look and feel
Each slider illustrates characteristics of the customer's brand and the style your logo design should communicate.

```html
<!DOCTYPE html>
<html lang="en">
<head>
<meta charset="utf-8">
<title>Velour Music Productions</title>
<link rel="stylesheet" href="https://fonts.googleapis.com/css2?family=Cuprum:wght@400;700&family=PT+Sans:wght@400;700&display=swap">
<style>
:root{
  --black:#0b0b0b;
  --panel:#111;
  --wood:#3b3b3b;
  --wood-dark:#303030;
  --gold:#d2a63a;
  --gold-light:#e6c25a;
  --gold-dark:#a9802a;
  --text:#e2e2e2;
  --muted:#c8c8c8;
  --field:#555;
  --field-border:#777;
  --footer:#2f2f2f;
}
*{box-sizing:border-box;margin:0;padding:0}
html,body{width:882px;height:1200px;overflow:hidden}
body{position:relative;font-family:"PT Sans",sans-serif;color:var(--text);
  background:linear-gradient(90deg,var(--wood-dark),var(--wood) 30%,#404040 60%,var(--wood-dark));}
.abs{position:absolute}
.header{left:0;top:0;width:882px;height:95px;background:var(--black);border-bottom:1px solid #222}
.brand{left:114px;top:34px;display:flex;align-items:center;gap:8px}
.brand-mark{width:14px;height:14px;border-radius:50%;background:var(--gold)}
.brand-name{font-family:"Cuprum",sans-serif;font-size:22px;color:var(--gold);letter-spacing:1px}
.brand-sub{left:117px;top:62px;font-family:"Cuprum",sans-serif;font-size:9px;letter-spacing:2.5px;color:#ddd}
.search{left:456px;top:14px;width:125px;height:18px;background:#9a9a9a;border:1px solid #bbb;font-size:8px;font-style:italic;color:#eee;padding:4px 9px}
.btn-login{left:616px;top:12px;width:69px;height:24px;background:var(--gold);color:#222;font-size:10.5px;display:flex;align-items:center;justify-content:center;gap:6px}
.btn-register{left:691px;top:12px;width:87px;height:24px;background:#666;color:#eee;font-size:10.5px;display:flex;align-items:center;justify-content:center;gap:6px}
.nav a{position:absolute;top:67px;font-size:11px;color:#fff;text-decoration:none;transform:translateX(-50%);white-space:nowrap}
.nav .home{left:404px;top:54px;width:52px;height:41px;background:linear-gradient(#e0b54a,#b98d2e);border-radius:6px 6px 0 0;transform:none;text-align:center;padding-top:13px}
.slider{left:106px;top:118px;width:467px;height:254px;background:linear-gradient(120deg,#b06a3a,#e9c19a 35%,#c9977a 55%,#6a3b26);overflow:hidden}
.slide-arrow{top:113px;width:44px;height:45px;background:rgba(30,30,30,.75)}
.slider-caption{left:28px;top:220px;font-family:"Cuprum",sans-serif;font-size:21px;font-variant:small-caps;color:#fff;text-shadow:0 1px 3px #000,0 0 2px #000}
.form-panel{left:586px;top:118px;width:204px;height:256px;background:var(--panel)}
.panel-title{font-family:"Cuprum",sans-serif;font-variant:small-caps;color:var(--gold);font-size:15px}
.field{position:absolute;height:24px;background:var(--field);border:1px solid var(--field-border);font-size:8px;color:#eee;padding:7px 10px}
.btn-submit{left:132px;top:189px;width:62px;height:24px;background:linear-gradient(var(--gold-light),var(--gold-dark));border-radius:6px;border:1px solid #f1d27a;font-family:"Cuprum",sans-serif;font-variant:small-caps;font-size:13px;color:#fff;text-align:center;line-height:21px}
.form-note{left:8px;top:218px;width:190px;font-size:7.2px;line-height:10.4px;color:#eee}
h2.section{font-family:"Cuprum",sans-serif;font-weight:400;color:#eee}
h2.section span{color:var(--gold)}
.dots{height:0;border-top:1px dotted #777}
.para{font-size:8.5px;line-height:15.5px;color:var(--muted)}
.btn-more{left:482px;top:536px;width:67px;height:24px;background:var(--gold);font-family:"Cuprum",sans-serif;font-weight:700;font-size:11px;color:#fff;text-align:center;line-height:24px;border-radius:2px}
.action{left:586px;width:204px;background:linear-gradient(#e3c27a,#a98530);border:2px solid #d8c28a;display:flex;align-items:center;gap:14px;padding-left:10px;font-family:"Cuprum",sans-serif;font-variant:small-caps;font-weight:700;color:#fff;font-size:19px;line-height:20px;text-shadow:0 1px 2px #5a4312}
.reviews{left:586px;top:578px;width:204px;height:450px;background:#2d2d2d;border:1px solid #555}
.reviews-head{height:36px;background:var(--black);padding:9px 15px}
.review{position:absolute;left:5px;width:192px}
.review-img{position:absolute;left:0;top:0;width:67px;height:82px;border:1px solid #888}
.review-body{position:absolute;left:72px;top:0;width:120px}
.review-count{font-size:8px;color:var(--gold)}
.review-title{font-size:10px;color:#eee;margin-top:4px;white-space:nowrap}
.review-text{font-size:7.4px;line-height:8.6px;color:#ddd;margin-top:5px;text-align:justify}
.review-more{font-size:8px;color:var(--gold);margin:6px 0 0 4px}
.video{left:105px;top:640px;width:256px;height:146px;background:linear-gradient(135deg,#8a8a8a,#3a3a3a 50%,#1c1c1c);border:3px solid #111}
.video-title{left:6px;top:6px;font-size:7.5px;font-weight:700;color:#fff}
.video-bar{left:0;bottom:0;width:100%;height:20px;background:rgba(10,10,10,.8)}
.more-link{font-size:8.5px;color:var(--gold)}
.demo{position:absolute;top:875px;width:120px}
.demo-img{height:68px;border:1px solid #aaa}
.demo-title{font-size:10px;color:#eee;margin-top:12px}
.demo-text{font-size:8px;line-height:10.3px;color:#ddd;margin-top:6px;text-align:justify}
.footer{left:0;top:1058px;width:882px;height:100px;background:var(--footer)}
.footer-title{font-family:"Cuprum",sans-serif;font-size:15px;color:#eee}
.news-input{left:121px;top:1108px;width:189px;height:23px;background:#fff;border:1px solid #bbb;font-size:8px;font-style:italic;color:#888;padding:6px 11px}
.btn-subscribe{left:317px;top:1109px;width:76px;height:23px;background:var(--gold);font-family:"Cuprum",sans-serif;font-weight:700;font-size:10.5px;color:#fff;text-align:center;line-height:23px}
.social{top:1109px;width:19px;height:19px;border:1px solid #ccc}
.bottom{left:0;top:1158px;width:882px;height:42px;background:var(--black);text-align:center;font-size:8px;color:#ccc;padding-top:9px;line-height:18px}
</style>
</head>
<body>

<header class="abs header">
  <div class="abs brand"><span class="brand-mark"></span><span class="brand-name">VELOUR</span></div>
  <div class="abs brand-sub">MUSIC PRODUCTIONS</div>
  <div class="abs search">Search</div>
  <div class="abs btn-login">
    <svg width="9" height="11" viewBox="0 0 9 11"><rect x="0" y="4" width="9" height="7" fill="#222"/><path d="M2 4V2.5a2.5 2.5 0 0 1 5 0V4" stroke="#222" fill="none" stroke-width="1.4"/></svg>Login</div>
  <div class="abs btn-register">
    <svg width="10" height="10" viewBox="0 0 10 10"><rect x="0.5" y="1.5" width="9" height="8" fill="none" stroke="#ddd"/><path d="M2 4h6M2 6h6" stroke="#ddd"/></svg>Register</div>
  <nav class="nav">
    <a class="home" href="#">Home</a>
    <a href="#" style="left:491px">About Us</a>
    <a href="#" style="left:555px">Services</a>
    <a href="#" style="left:614px">Videos</a>
    <a href="#" style="left:684px">Music Demos</a>
    <a href="#" style="left:757px">Contact</a>
  </nav>
</header>

<section class="abs slider" role="img" aria-label="Rotating header photo of young singers sharing a microphone">
  <div class="abs slide-arrow" style="left:1px"><svg width="44" height="45"><path d="M25 15l-7 8 7 8" stroke="#d2a63a" stroke-width="3" fill="none"/></svg></div>
  <div class="abs slide-arrow" style="right:1px"><svg width="44" height="45"><path d="M19 15l7 8-7 8" stroke="#444" stroke-width="3" fill="none"/></svg></div>
  <div class="abs slider-caption">We turn aspiring musicians into SuperStars!</div>
</section>

<aside class="abs form-panel">
  <div class="abs panel-title" style="left:8px;top:6px">Contact Us or Submit Music Demo</div>
  <div class="field" style="left:8px;top:32px;width:89px">First Name*</div>
  <div class="field" style="left:107px;top:32px;width:88px">Last Name*</div>
  <div class="field" style="left:8px;top:63px;width:89px">Age</div>
  <div class="field" style="left:107px;top:63px;width:88px">Zip Code</div>
  <div class="field" style="left:8px;top:92px;width:187px">Email Address*</div>
  <div class="field" style="left:8px;top:122px;width:89px">Daytime Phone</div>
  <div class="field" style="left:107px;top:122px;width:88px">Evening Phone</div>
  <div class="field" style="left:8px;top:152px;width:187px;height:31px">Comments</div>
  <div class="abs btn-submit">Submit</div>
  <p class="abs form-note">After submitting, you will have the opportunity to upload demos of your music (optional) provide other pertinent information about yourself, band, or group.</p>
</aside>

<h2 class="abs section" style="left:106px;top:403px;font-size:19px">Welcome to <span>&nbsp;Our Site</span></h2>
<div class="abs dots" style="left:106px;top:432px;width:320px"></div>
<p class="abs" style="left:110px;top:443px;font-size:10.5px;color:#fff">Mauris vel lacus vitae felis vestibulum volutpat. Etiam est nunc, venisl.</p>
<p class="abs para" style="left:110px;top:464px;width:443px">Sed ut perspiciatis unde omnis iste natus error sit voluptatem accusantium doloremque laudantium, totam rem aperiam, eaque ipsa quae ab illo inventore veritatis et quasi architecto beatae vitae dicta sunt explicabo. Nemo enim ipsam voluptatem quia voluptas sit aspernatur aut odit aut fugit, sed quia consequuntur magni dolores eos qui ratione voluptatem sequi nesciunt. Neque porro quisquam est, qui dolorem ipsum quia dolor sit amet.Sed ut perspiciatis unde omnis iste natus error sit voluptatem accusantium doloremque.</p>
<div class="abs btn-more">More</div>

<div class="abs action" style="top:408px;height:67px">
  <svg width="48" height="36" viewBox="0 0 48 36"><path d="M10 6h34v24H14l-4-4z" fill="none" stroke="#111" stroke-width="3"/><path d="M18 14h20M18 20h16" stroke="#111" stroke-width="3"/><path d="M4 4l14 14" stroke="#111" stroke-width="4"/></svg>
  <span>Create A Profile</span></div>
<div class="abs action" style="top:492px;height:66px">
  <svg width="40" height="40" viewBox="0 0 40 40"><circle cx="20" cy="20" r="19" fill="#111"/><path d="M20 8l-9 10h6v12h6V18h6z" fill="#e6c25a"/></svg>
  <span>Upload<br>Music Demo</span></div>

<aside class="abs reviews">
  <div class="reviews-head panel-title" style="font-size:16px">Our Reviews</div>
  <div class="review" style="top:40px">
    <div class="review-img" role="img" aria-label="Vintage studio microphone" style="background:linear-gradient(135deg,#3a3a1a,#b32020 50%,#2a6a2a)"></div>
    <div class="review-body"><div class="review-count">15 Reviews</div><div class="review-title">Sed Perspiciatis Unde Omni</div><p class="review-text">voluptatem laudantium, totam rem aperiam, eaque ipsa quae ab inventore veritatisvoluptatem .</p><div class="review-more">MORE &gt;&gt;</div></div>
  </div>
  <div class="review" style="top:143px">
    <div class="review-img" role="img" aria-label="Singer with acoustic guitar on stage" style="background:linear-gradient(135deg,#555,#8a8a8a 50%,#2a3a5a)"></div>
    <div class="review-body"><div class="review-count">22 Reviews</div><div class="review-title">Sed Perspiciatis Unde Omni</div><p class="review-text">voluptatem laudantium, totam rem aperiam, eaque ipsa quae ab inventore veritatisvoluptatem .</p><div class="review-more">MORE &gt;&gt;</div></div>
  </div>
  <div class="review" style="top:247px">
    <div class="review-img" role="img" aria-label="Vocalists performing on stage" style="background:linear-gradient(135deg,#5a3a2a,#c89070 50%,#3a2a2a)"></div>
    <div class="review-body"><div class="review-count">25 Reviews</div><div class="review-title">Sed Perspiciatis Unde Omni</div><p class="review-text">voluptatem laudantium, totam rem aperiam, eaque ipsa quae ab inventore veritatisvoluptatem .</p><div class="review-more">MORE &gt;&gt;</div></div>
  </div>
  <div class="review" style="top:351px">
    <div class="review-img" role="img" aria-label="Producer at recording studio keyboard" style="background:linear-gradient(135deg,#222,#777 50%,#aa4a3a)"></div>
    <div class="review-body"><div class="review-count">a2 Reviews</div><div class="review-title">Sed Perspiciatis Unde Omni</div><p class="review-text">voluptatem laudantium, totam rem aperiam, eaque ipsa quae ab inventore veritatisvoluptatem .</p><div class="review-more">MORE &gt;&gt;</div></div>
  </div>
</aside>

<h2 class="abs section" style="left:110px;top:593px;font-size:16px;font-weight:700">OUR <span>VIDEO</span></h2>
<div class="abs dots" style="left:110px;top:622px;width:430px"></div>
<div class="abs video" role="img" aria-label="Video player showing a hand on a mixing desk">
  <div class="abs video-title">Music Production Overview</div>
  <div class="abs video-bar">
    <svg width="250" height="20"><path d="M20 5l8 5-8 5z" fill="#8ab0d8"/><text x="50" y="13" font-size="6" fill="#ccc" font-family="PT Sans">00:00</text><rect x="70" y="9" width="110" height="2" fill="#777"/><text x="182" y="13" font-size="6" fill="#ccc" font-family="PT Sans">03:33</text><rect x="214" y="6" width="7" height="7" fill="none" stroke="#8ab0d8"/><path d="M232 8h3l3-3v10l-3-3h-3z" fill="#8ab0d8"/></svg>
  </div>
</div>
<p class="abs para" style="left:374px;top:640px;width:174px;line-height:13.2px;text-align:justify">Sed ut perspiciatis unde omnis iste natus error sit voluptatem accusantium doloremque laudantium, totam rem aperiam, eaque ipsa quae ab illo inventore veritatis et quasi architecto beatae vitae dicta sunt explicabo.<br><br>Nemo enim ipsam voluptatem quia voluptas sit aspernatur aut odit aut fugit, sed quia consequuntur magni dolores eos qui ratione voluptatem sequi nesciunt.</p>
<div class="abs more-link" style="left:513px;top:773px">More &gt;&gt;</div>

<h2 class="abs section" style="left:114px;top:821px;font-size:16px;font-weight:700">MUSIC <span>DEMOS</span></h2>
<svg class="abs" style="left:504px;top:824px" width="42" height="14"><path d="M0 7l7-6v4h8v4H7v4z" fill="#bbb"/><path d="M42 7l-7-6v4h-8v4h8v4z" fill="#ddd"/></svg>
<div class="abs dots" style="left:114px;top:850px;width:426px"></div>
<div class="demo" style="left:121px">
  <div class="demo-img" role="img" aria-label="Band playing guitars on a red-lit stage" style="background:linear-gradient(135deg,#3a1010,#b03030 50%,#221)"></div>
  <div class="demo-title">Bass Player Needed Band</div>
  <p class="demo-text">Nemo enim ipsam voluptatem quia voluptas sit aspernatur aut odit aut fugit, sed quia consequuntur magni dolores</p>
  <div class="more-link" style="margin-top:8px">More &gt;&gt;</div>
</div>
<div class="demo" style="left:268px">
  <div class="demo-img" role="img" aria-label="Band performing under purple stage lights" style="background:linear-gradient(135deg,#1a2a1a,#8a2a8a 55%,#1a1a2a)"></div>
  <div class="demo-title">Bass Player Needed Band</div>
  <p class="demo-text">Nemo enim ipsam voluptatem quia voluptas sit aspernatur aut odit aut fugit, sed quia consequuntur magni dolores</p>
  <div class="more-link" style="margin-top:8px">More &gt;&gt;</div>
</div>
<div class="demo" style="left:421px">
  <div class="demo-img" role="img" aria-label="Drum kit and amplifiers on an empty stage" style="background:linear-gradient(180deg,#1a1a1a,#3a3a4a 55%,#b0702a)"></div>
  <div class="demo-title">Bass Player Needed Band</div>
  <p class="demo-text">Nemo enim ipsam voluptatem quia voluptas sit aspernatur aut odit aut fugit, sed quia consequuntur magni dolores</p>
  <div class="more-link" style="margin-top:8px">More &gt;&gt;</div>
</div>

<footer class="abs footer"></footer>
<div class="abs footer-title" style="left:121px;top:1079px">Newsletter</div>
<div class="abs news-input">Your Email Id</div>
<div class="abs btn-subscribe">Subscribe</div>
<div class="abs footer-title" style="left:622px;top:1079px">Connect With Us</div>
<div class="abs social" style="left:622px;background:#3b5a9a"></div>
<div class="abs social" style="left:651px;background:#3aa8dc"></div>
<div class="abs social" style="left:679px;background:#eee"></div>
<div class="abs social" style="left:708px;background:#e8902a"></div>
<div class="abs social" style="left:736px;background:#c82020"></div>
<div class="abs social" style="left:765px;background:#8aa0b8"></div>

<div class="abs bottom">Privacy &nbsp;|&nbsp; Help &nbsp;|&nbsp; Terms &amp; Conditions<br>© 2013 Velour. All rights reserved</div>

</body>
</html>
```